Pellowar

We need logo and wesbsite for a software development company based out of Hyderabad, India focused on startups and mid sized companies focused on build a new software products in USA and Europe countires.

Target Market(s)

startup and midsized companies in teh USA and Europe for software product development.

Industry/Entity Type

software development

Coding

Coded - Design and coding required

Number of Pages Required

5+ page

Requirements
Must have
• latest design concepts and very elegant
Nice to have
• each page should have images that reflects the content
Should not have
• too many colors

```html
<!DOCTYPE html>
<html lang="en">
<head>
<meta charset="utf-8">
<title>Pellowar — About Us</title>
<link href="https://fonts.googleapis.com/css2?family=Open+Sans:wght@300;400;600&display=swap" rel="stylesheet">
<style>
  :root{
    --orange:#e58e12;
    --red:#b03c28;
    --blue:#1f6aa0;
    --ink:#222222;
    --text:#333333;
    --muted:#555555;
    --soft:#f4f4f4;
    --band:#f0f0f0;
    --disc:#dddddd;
  }
  *{box-sizing:border-box;margin:0;padding:0}
  html,body{width:1200px;height:2281px;overflow:hidden;background:#fff}
  body{position:relative;font-family:"Open Sans",sans-serif;color:var(--text)}
  .abs{position:absolute}

  .site-header{position:absolute;left:0;top:0;width:1200px;height:93px;background:#fff}
  .brand{position:absolute;left:97px;top:30px;display:flex;align-items:center;gap:10px;font-weight:600;font-size:30px;color:var(--ink);letter-spacing:-0.5px}
  .brand-dot{width:34px;height:34px;border-radius:50%;background:var(--orange)}
  .main-nav a{position:absolute;top:48px;font-size:12.5px;color:var(--ink);text-decoration:none;white-space:nowrap}
  .main-nav a.is-active{color:var(--orange)}
  .nav-underline{left:641px;top:88px;width:49px;height:3px;background:var(--orange)}

  .hero{left:0;top:93px;width:1200px;height:370px;
    background:linear-gradient(135deg,#cfcac3 0%,#6e4a32 30%,#5a3a26 55%,#b9b3ac 80%,#d8d4cf 100%)}

  .page-title{left:0;top:520px;width:1200px;text-align:center;font-weight:300;font-size:52px;color:var(--ink);line-height:1.1}
  .title-rule{left:532px;top:599px;width:135px;height:3px;background:var(--orange)}

  .lead{left:125px;top:670px;width:300px;font-weight:300;font-size:22px;line-height:28px;color:var(--ink)}
  .about-copy{left:478px;top:673px;width:555px;font-size:13.4px;line-height:23.5px;color:var(--text)}
  .about-copy p{margin-bottom:23.5px}

  .model{left:0;top:1191px;width:1200px;height:671px;background:var(--soft)}
  .model h2{position:absolute;left:0;top:74px;width:1200px;text-align:center;font-weight:300;font-size:28px;color:var(--ink)}
  .model-chart{position:absolute;left:0;top:0}
  .chart-label{font-family:"Open Sans",sans-serif;font-weight:300;font-size:22px;fill:var(--ink)}
  .chart-axis{font-family:"Open Sans",sans-serif;font-weight:300;font-size:18px;fill:#555}
  .chart-step{font-family:"Open Sans",sans-serif;font-size:13px;fill:#555}

  .site-footer{left:0;top:1862px;width:1200px;height:331px;background:#fff}
  .footer-brand{position:absolute;left:95px;top:108px;display:flex;align-items:center;gap:14px;font-weight:600;font-size:44px;color:var(--ink);letter-spacing:-1px}
  .footer-brand .brand-dot{width:46px;height:46px}
  .footer-col{position:absolute;top:94px}
  .footer-col h3{font-weight:300;font-size:23px;color:var(--ink);line-height:1}
  .footer-col .rule{width:48px;height:2px;background:var(--orange);margin-top:10px}
  .links{list-style:none;margin-top:13px}
  .links li{font-size:12.5px;line-height:23.5px;color:var(--ink)}
  .links li::before{content:"»";color:var(--orange);margin-right:8px}
  .links li.is-active{color:var(--orange)}
  .contact-item{position:relative;padding-left:20px;margin-top:14px;font-size:13.5px;line-height:20px;color:var(--muted)}
  .contact-item:first-of-type{margin-top:16px}
  .contact-item strong{display:block;font-weight:600;color:var(--ink)}
  .contact-item svg{position:absolute;left:0;top:3px}

  .copyright{left:0;top:2193px;width:1200px;height:88px;background:var(--band);text-align:center;line-height:88px;font-size:11px;letter-spacing:4.5px;color:#444}
</style>
</head>
<body>

<header class="site-header">
  <div class="brand"><span class="brand-dot"></span>Pellowar</div>
  <nav class="main-nav">
    <a style="left:583px">Home</a>
    <a style="left:641px" class="is-active">About Us</a>
    <a style="left:716px">Build Your Product</a>
    <a style="left:844px">Build Your team</a>
    <a style="left:956px">Case Study</a>
    <a style="left:1041px">Contact Us</a>
  </nav>
  <div class="abs nav-underline"></div>
</header>

<div class="abs hero" role="img" aria-label="Overhead photo of a team around a wooden table with laptops, shaking hands"></div>

<h1 class="abs page-title">About Us</h1>
<div class="abs title-rule"></div>

<p class="abs lead">Teams are the essence of every business.<br>They can create wonders if built with perfection.</p>

<div class="abs about-copy">
  <p>Teams are the essence of every business. They can create wonders if built with perfec-tion.</p>
  <p>We are a group of entrepreneurs, technocrats, software architects, and delivery heads who have come together to serve startups, product companies, and enterprises with their product development. We are prompt in understanding your product and help design, build, maintain and operate your product. Pellowar quickly set up a team of UX experts, Business Analysts, Developers and QA resources to build the best team to deliver the product.</p>
  <p>Businesses can focus on core activities of Sales and Marketing to achieve revenue growth, and we will accelerate in your go-to-market.</p>
  <p>Building software products or solutions is changing day by day. The entire process is very extensive and cumbersome. Developing software requires a level of expertise that our team possesses.</p>
  <p>While start up teams and small sized companies are struggling to build software from scratch, others are way ahead in their game. This is where we come in and uplift you. We come bearing the best resources, robust design, and scalable technology.</p>
</div>

<section class="abs model">
  <h2>Team Technology and Process Model for Product development</h2>
  <svg class="model-chart" width="1200" height="671" viewBox="0 1191 1200 671" aria-label="Team, process and technology model">
    <path d="M549 1400 A159 159 0 0 0 549 1718 Z" fill="var(--disc)"/>
    <path d="M549 1559 L549 1384 A175 175 0 0 1 687 1451 Z" fill="var(--orange)"/>
    <path d="M549 1559 L680 1457 A166 166 0 0 1 676 1666 Z" fill="var(--red)"/>
    <path d="M549 1559 L672 1662 A161 161 0 0 1 549 1720 Z" fill="var(--blue)"/>

    <g fill="#fff">
      <circle cx="600" cy="1448" r="8"/><circle cx="585" cy="1452" r="6"/><circle cx="615" cy="1452" r="6"/>
      <path d="M586 1480 q14 -22 28 0 Z"/><path d="M577 1476 q8 -16 16 -6 v6 Z"/><path d="M607 1470 q8 -10 16 6 Z"/>
    </g>
    <g fill="none" stroke="#fff" stroke-width="4">
      <circle cx="651" cy="1554" r="16"/>
      <circle cx="666" cy="1566" r="7"/>
      <path d="M627 1580 v-20 M663 1532 l21 -16 M684 1516 v12"/>
    </g>
    <g fill="none" stroke="#fff" stroke-width="3">
      <rect x="595" y="1634" width="20" height="32" rx="3"/>
      <path d="M605 1648 l14 12 l-6 6"/>
    </g>

    <circle cx="549" cy="1559" r="57" fill="#ececec" stroke="#aaa" stroke-width="1.5"/>
    <g stroke="#aaa" stroke-width="1">
      <line x1="549" y1="1502" x2="549" y2="1616"/>
      <line x1="549" y1="1559" x2="594" y2="1524"/>
      <line x1="549" y1="1559" x2="593" y2="1596"/>
    </g>
    <path d="M512 1559 h16 M522 1551 l8 8 l-8 8" fill="none" stroke="#444" stroke-width="4"/>
    <text class="chart-step" x="558" y="1533">01</text>
    <text class="chart-step" x="575" y="1564">02</text>
    <text class="chart-step" x="556" y="1595">03</text>

    <text class="chart-axis" transform="translate(447 1559) rotate(-90)" text-anchor="middle">Product</text>
    <text class="chart-axis" transform="translate(469 1559) rotate(-90)" text-anchor="middle">Development</text>

    <text class="chart-label" x="659" y="1411">Team</text>
    <text class="chart-label" x="732" y="1569">Process</text>
    <text class="chart-label" x="645" y="1716">Technology</text>
  </svg>
</section>

<footer class="abs site-footer">
  <div class="footer-brand"><span class="brand-dot"></span>Pellowar</div>
  <div class="footer-col" style="left:443px">
    <h3>Main Links</h3>
    <div class="rule"></div>
    <ul class="links">
      <li>Home</li>
      <li class="is-active">About Us</li>
      <li>Our Products</li>
      <li>Our Team</li>
      <li>Case Study</li>
      <li>Contact Us</li>
    </ul>
  </div>
  <div class="footer-col" style="left:750px">
    <h3>Contact Us</h3>
    <div class="rule"></div>
    <div class="contact-item">
      <svg width="12" height="15" viewBox="0 0 12 15"><path d="M6 0a6 6 0 0 0-6 6c0 4 6 9 6 9s6-5 6-9a6 6 0 0 0-6-6z" fill="var(--orange)"/><circle cx="6" cy="6" r="2.2" fill="#fff"/></svg>
      <strong>Address:</strong>48 Harlow Lane Denton, TX 40117
    </div>
    <div class="contact-item">
      <svg width="14" height="14" viewBox="0 0 14 14"><path d="M3 1l3 3-2 2q1.5 3 4 4l2-2 3 3-2 2Q5 12 1 3z" fill="none" stroke="var(--orange)" stroke-width="1.5"/></svg>
      <strong>Phone:</strong>1-800-555-01-42
    </div>
    <div class="contact-item">
      <svg width="15" height="11" viewBox="0 0 15 11"><rect width="15" height="11" fill="var(--orange)"/><path d="M0 0l7.5 6L15 0" fill="none" stroke="#fff" stroke-width="1.3"/></svg>
      <strong>Mail:</strong>hello@pellowar.example
    </div>
  </div>
</footer>

<div class="abs copyright">COPYRIGHT © 2022 PELLOWAR</div>

</body>
</html>
```